Shipping and Logistics, Project

Project description : Company Profile

A total logistics company covering domestic / international freight forwarding, warehouse management services, haulage, supply chain management, transport management & distribution, procurement & assembly services, shipping, chartering & bunker services, project logistics & tax exemption consultancy, oil & gas logistics, halal logistics services & integrated logistics management. We’re a well-established and experienced freight forwarder in Kuala Lumpur, Malaysia. We specialize in customized value-added solution that optimizes your supply chain by trimming inventory, reducing logistics cost and enhancing your customer service levels.

As a member of the Worldwide Parcel and Carriage Alliance which comprise of 170 global freight agents in 80 countries that promotes great handling in cross-trade logistics and freighting. You could rely on our efficiency in handlings of export cargo (FCL, LCL, Bulk and Conventional) between our global network offices worldwide with a total scale of 10,000 groomed specialists in various logistics division working together to ensure delivery task meets with your expectation. With our dedicated qualified and experienced professionals, we are fully committed to serving our clients.

Our generic services are listed below for your reference:

• Air Freight
• Ocean Freight FCL & LCL
• Container Haulage
• Warehousing
• Transportation and Distribution within Malaysia and Thailand
• Cross-Border Road Line-hauls between Thailand, Malaysia, Singapore and Laos
• Customs Brokerage and Forwarding
• Project Cargo Freight Forwarding for setting up of new plants / factories and ad hoc heavy-lift
• Air-Sea-Road-Rail multi-modal options
• Import / Export / Storage / Documentation / Handling of DG / Hazmat
• Vessel and Aircraft Charters

Our Mission
Based on the motto “Quick, Reliable and Polite”, we are dedicated to upholding the following three points corporate philosophy:
1. Adhering to the principle that “the customer always comes first”.
2. Contributing to the development of the local community.
3. Making it our duty to be responsible and sincere.

Our Edge
• One-Stop Logistics Solutions
• Extensive Network Throughout Malaysia
• Highly Qualified and Experienced Pool of Professionals
• Comprehensive IT Solutions
• Innovative and Customer-focused Solutions
• Flexible and Consistent in Managing Exceptions
• Total Supply Chain Visibility

Target Market
1. We sell the logistics services to all the industry in Malaysia and Worldwide. (ONE Stop Logistics Solutions)

Competitor
1. TR Valmont
2. Corvessa Transport
3. Brandt + Loewe
4. FELRO
5. QTV
6. Routemarks
7. Ilto Logistics

Rules for Picking a Company Name
1. Unique and unforgettable
2. Avoid unusual spellings
3. Easy to pronounce and remember
4. Keep it simple
5. Make some sense
6. Give a clue

Rules for Picking a Company Logo
4. Keep it simple
5. Make some sense
6. Give a clue

1. Simplicity
2. Memorability
3. Originality
4. Modern Yet Timeless
5. Balance
6. Complementary
7. Versatility

Stationery Information
1. Company Name : ZENFreight Solutions Sdn Bhd
2. Company Registration : 2837165-W
3. Address : 42-08, Jalan Cempaka Indah 5, Taman Seri Bayu, 81300 Johor Bahru, Johor, Malaysia.
4. Name : Derek Tan
5. Position : Manager
6. Mobile No : (+6019) 4381907
7. Office No : (+607) 5218764
8. Fax No : Not Available
9. Email Address : derek.tan@zenfreight-solutions.example
10. Web Domain : www.zenfreight-solutions.example
11. Company Slogan : Be Globally Connected

Target Market(s)

Corporate Company

Industry/Entity Type

Shipping and Logistics Industry

Requirements
Must have
• Company Full Name : ZENFREIGHT SOLUTIONS SDN. BHD.
Nice to have
• Keep it simple and unforgettable ...

```html
<!DOCTYPE html>
<html lang="en">
<head>
<meta charset="utf-8">
<title>ZENFreight Solutions Stationery</title>
<link href="https://fonts.googleapis.com/css2?family=Poppins:wght@400;500&display=swap" rel="stylesheet">
<style>
:root{
  --stage:#c8c8c8;
  --paper:#ffffff;
  --brand-blue:#3d88c8;
  --ink:#222222;
  --rule:#b9c9da;
}
*{margin:0;padding:0;box-sizing:border-box}
html,body{width:1200px;height:900px;overflow:hidden}
body{background:var(--stage);font-family:"Poppins",sans-serif;color:var(--ink);position:relative}
.sheet{position:absolute;background:var(--paper)}
.brand{position:absolute;display:flex;align-items:center;gap:5px;color:var(--brand-blue);font-weight:500;font-family:"Poppins",sans-serif}
.brand-square{background:var(--brand-blue);flex:none}
.brand-name{line-height:1.05}
.brand-name .sub{display:block;letter-spacing:.18em}
/* folder cover */
.cover{left:114px;top:145px;width:314px;height:436px}
.cover .brand{left:83px;top:58px}
.cover .brand-square{width:40px;height:40px}
.cover .brand-name{font-size:17px}
.cover .brand-name .sub{font-size:6.5px;margin-top:4px}
.cover-tagline{position:absolute;left:0;right:0;top:399px;display:flex;align-items:center;gap:6px;font-size:8.5px;letter-spacing:.18em;white-space:nowrap}
.cover-tagline::before,.cover-tagline::after{content:"";flex:1;height:1px;background:var(--rule)}
/* letterhead */
.letterhead{left:460px;top:154px;width:291px;height:425px}
.letterhead .brand{left:24px;top:11px}
.letterhead .brand-square{width:26px;height:26px}
.letterhead .brand-name{font-size:11px}
.letterhead .brand-name .sub{font-size:4.2px;margin-top:2px}
.letterhead-tagline{position:absolute;right:0;top:19px;display:flex;align-items:center;gap:4px;color:var(--brand-blue);font-size:5.6px;font-weight:500}
.letterhead-tagline::after{content:"";width:14px;height:6px;background:var(--brand-blue)}
.letterhead-footer{position:absolute;left:0;right:0;bottom:0;height:30px;background:var(--brand-blue);color:#fff;font-size:5.2px;line-height:1.2;display:flex;align-items:center;padding-left:24px}
.footer-col{padding:0 5px;border-left:0.5px solid rgba(255,255,255,.7)}
.footer-col:first-child{padding-left:0;border-left:none}
/* envelopes */
.flap{position:absolute}
.envelope-large{left:786px;top:152px;width:307px;height:430px}
.envelope-large .brand{left:25px;top:36px}
.envelope-large .brand-square{width:26px;height:26px}
.envelope-large .brand-name{font-size:11px}
.envelope-large .brand-name .sub{font-size:4.2px;margin-top:2px}
.envelope-large-rule{position:absolute;left:26px;right:27px;top:405px;height:1px;background:var(--rule)}
.envelope-large-address{position:absolute;left:0;right:0;top:413px;text-align:center;font-size:5.3px}
.envelope-dl{left:436px;top:650px;width:340px;height:170px}
.envelope-dl .brand{left:17px;top:22px}
.envelope-dl .brand-square{width:22px;height:22px}
.envelope-dl .brand-name{font-size:9.5px}
.envelope-dl .brand-name .sub{font-size:3.6px;margin-top:2px}
.envelope-dl-address{position:absolute;left:19px;top:138px;font-size:5.3px;line-height:1.25}
</style>
</head>
<body>

<section class="sheet cover">
  <div class="brand"><span class="brand-square"></span><span class="brand-name">ZENFREIGHT<span class="sub">SOLUTIONS SDN. BHD.</span></span></div>
  <p class="cover-tagline">BE GLOBALLY CONNECTED</p>
</section>

<section class="sheet letterhead">
  <div class="brand"><span class="brand-square"></span><span class="brand-name">ZENFREIGHT<span class="sub">SOLUTIONS SDN. BHD.</span></span></div>
  <p class="letterhead-tagline">BE GLOBALLY CONNECTED</p>
  <footer class="letterhead-footer">
    <div class="footer-col">P: (+6019) 438 1907<br>M: +607) 521 8764</div>
    <div class="footer-col">E: derek.tan@zenfreight-solutions.example<br>W: www.zenfreight-solutions.example</div>
    <div class="footer-col">42-08, Jalan Cempaka Indah 5<br>Taman Seri Bayu, 81300<br>Johor Bahru, Johor, Malaysia.</div>
  </footer>
</section>

<svg class="flap" style="left:786px;top:93px" width="307" height="62" viewBox="0 0 307 62">
  <polygon points="32,0 237,0 307,53 307,61 0,57 0,55" fill="var(--brand-blue)"/>
</svg>
<section class="sheet envelope-large">
  <div class="brand"><span class="brand-square"></span><span class="brand-name">ZENFREIGHT<span class="sub">SOLUTIONS SDN. BHD.</span></span></div>
  <div class="envelope-large-rule"></div>
  <p class="envelope-large-address">42-08, Jalan Cempaka Indah 5, Taman Seri Bayu, 81300 Johor Bahru, Johor, Malaysia.</p>
</section>

<svg class="flap" style="left:436px;top:624px" width="340" height="26" viewBox="0 0 340 26">
  <polygon points="15,0 322,0 340,26 0,26" fill="var(--brand-blue)"/>
</svg>
<section class="sheet envelope-dl">
  <div class="brand"><span class="brand-square"></span><span class="brand-name">ZENFREIGHT<span class="sub">SOLUTIONS SDN. BHD.</span></span></div>
  <p class="envelope-dl-address">42-08, Jalan Cempaka Indah 5,<br>Taman Seri Bayu, 81300 Johor<br>Bahru, Johor, Malaysia.</p>
</section>

</body>
</html>
```